Business Card Design for Training Business

Clear Path Coaching is a new business that delivers training and other services with a focus on topics related to mental health and wellbeing, for example, Wellmind Response Course, Resilience etc. We have a strong focus on evidence-based psychology and neuroscience. I have a logo which I will upload with the brief, so please consider colours that work well with the logo.
Target Market(s)
Adults, workplaces (particularly government and not-for-profits)
Industry/Entity Type
Business
Contact Information for Business Card
Head Strong TrainingSamantha SellwoodDirector0438 770 850sam@headstrongtraining.com.auwww.headstrongtraining.com.au

```html
<!DOCTYPE html>
<html lang="en">
<head>
<meta charset="utf-8">
<title>Clear Path Coaching – Business Card</title>
<link href="https://fonts.googleapis.com/css2?family=Arimo:wght@400;700&display=swap" rel="stylesheet">
<style>
  :root {
    --backdrop: #e9e7e4;
    --card: #1c1c1e;
    --card-edge: #151517;
    --teal: #22b5b8;
    --ink: #f1f1f1;
    --ink-soft: #c9c9cb;
    --brand-grey: #b9bcbf;
  }
  * { margin: 0; padding: 0; box-sizing: border-box; }
  html, body {
    width: 1200px; height: 787px; overflow: hidden;
    background: var(--backdrop);
    font-family: "Arimo", Arial, sans-serif;
  }
  .stage {
    width: 1200px; height: 787px;
    display: flex; align-items: center; justify-content: center; gap: 40px;
  }
  .card {
    position: relative;
    width: 540px; height: 330px;
    background: var(--card);
    border: 1px solid var(--card-edge);
    border-radius: 3px;
    box-shadow: 0 10px 28px rgba(0,0,0,.22);
  }

  /* Back side */
  .card-back .brand-disc {
    position: absolute; left: 176px; top: 70px;
    width: 120px; height: 120px; border-radius: 50%;
    border: 2px solid var(--teal);
  }
  .card-back .web {
    position: absolute; left: 60px; bottom: 62px;
    color: var(--ink); font-size: 14px; letter-spacing: .5px;
  }
  .card-back .brand-name {
    position: absolute; left: 0; right: 0; top: 206px;
    text-align: center; padding-right: 68px;
    color: var(--brand-grey); font-size: 14px; letter-spacing: 4px;
  }

  /* Front side */
  .person { position: absolute; left: 44px; top: 104px; }
  .person .name {
    color: var(--teal); font-weight: 700; font-size: 21px;
  }
  .person .role {
    color: var(--ink); font-size: 13px; margin-top: 3px;
  }
  .contacts {
    position: absolute; left: 44px; top: 178px;
    list-style: none;
  }
  .contacts li {
    display: flex; align-items: center; gap: 12px;
    color: var(--ink); font-size: 13.5px; height: 24px;
  }
  .contacts svg { width: 14px; height: 14px; flex: none; }

  .brand {
    position: absolute; right: 34px; top: 88px;
    width: 190px; text-align: center;
  }
  .brand .brand-disc {
    width: 76px; height: 76px; border-radius: 50%;
    border: 2px solid var(--teal); margin: 0 auto 14px;
  }
  .brand .brand-name {
    color: var(--brand-grey); font-size: 20px; letter-spacing: 3px;
    line-height: 1.35;
  }
</style>
</head>
<body>
<main class="stage">
  <section class="card card-back" aria-label="Card back">
    <div class="brand-disc"></div>
    <p class="brand-name">CLEAR PATH COACHING</p>
    <p class="web">www.clearpathcoaching.example.au</p>
  </section>

  <section class="card card-front" aria-label="Card front">
    <div class="person">
      <h1 class="name">Rebecca Tanfield</h1>
      <p class="role">Director</p>
    </div>
    <ul class="contacts">
      <li>
        <svg viewBox="0 0 16 16" aria-hidden="true"><path fill="var(--teal)" d="M3.6 1.5l2.3 2.3-1.3 1.8c.9 2 2.6 3.7 4.6 4.6l1.8-1.3 2.3 2.3-1.4 2.3C7.3 13.3 2.7 8.7 1.3 2.9z"/></svg>
        0491 362 517
      </li>
      <li>
        <svg viewBox="0 0 16 16" aria-hidden="true"><rect x="1" y="3.5" width="14" height="9" rx="1" fill="var(--teal)"/><path d="M1.5 4l6.5 5 6.5-5" fill="none" stroke="var(--card)" stroke-width="1.3"/></svg>
        bec@clearpathcoaching.example.au
      </li>
      <li>
        <svg viewBox="0 0 16 16" aria-hidden="true"><circle cx="8" cy="8" r="7" fill="var(--teal)"/><path d="M1 8h14M8 1c-3 3.5-3 10.5 0 14M8 1c3 3.5 3 10.5 0 14" fill="none" stroke="var(--card)" stroke-width="1"/></svg>
        www.clearpathcoaching.example.au
      </li>
    </ul>
    <div class="brand">
      <div class="brand-disc"></div>
      <p class="brand-name">CLEAR PATH<br>COACHING</p>
    </div>
  </section>
</main>
</body>
</html>
```